Heron Loan Partners Business Card

We need a business card design for our mortgage servicing company. In addition to servicing the loans of homeowners, we help homeowners with purchasing their homes and any mortgage refinancing. We would like to see designs that use the colors in the logo attached below (gold-ish yellow and navy blue), and any other design you deem fit! The design should communicate a simpler life with smart mortgages provided by Heron.

```html
<!DOCTYPE html>
<html lang="en">
<head>
<meta charset="UTF-8">
<title>Heron Loan Partners Business Card</title>
<link rel="stylesheet" href="https://fonts.googleapis.com/css2?family=Open+Sans:wght@400;600;700&display=swap">
<style>
  :root {
    --bg: #3a3a3a;
    --card-dark: #161616;
    --card-light: #ffffff;
    --gold: #e0b03c;
    --navy: #24205a;
    --ink: #1b1b2e;
  }
  * { margin: 0; padding: 0; box-sizing: border-box; }
  html, body { width: 1200px; height: 689px; overflow: hidden; }
  body {
    background: var(--bg);
    font-family: "Open Sans", sans-serif;
    position: relative;
  }
  .card {
    position: absolute;
    top: 196px;
    width: 520px;
    height: 297px;
    border-radius: 18px;
    overflow: hidden;
    box-shadow: 0 12px 30px rgba(0,0,0,.45);
  }
  .card--front { left: 50px; background: var(--card-dark); }
  .card--back { left: 630px; background: var(--card-light); }

  .wordmark {
    position: absolute;
    display: flex;
    align-items: center;
    gap: 12px;
    color: var(--gold);
    font-weight: 700;
    letter-spacing: 1px;
  }
  .wordmark__dot {
    width: 18px; height: 18px;
    border-radius: 50%;
    background: var(--gold);
  }
  .card--front .wordmark { left: 0; right: 0; top: 108px; justify-content: center; font-size: 62px; line-height: 1; }
  .card--back .wordmark { left: 0; right: 0; top: 46px; justify-content: center; font-size: 56px; line-height: 1; }

  .details {
    position: absolute;
    left: 60px;
    right: 40px;
    top: 150px;
    display: flex;
    align-items: stretch;
    gap: 18px;
  }
  .person { text-align: right; flex: 0 0 200px; color: var(--ink); font-size: 13px; line-height: 1.35; }
  .person__name { color: var(--gold); font-weight: 700; font-size: 19px; letter-spacing: .5px; line-height: 1.2; }
  .divider { width: 1.5px; background: var(--gold); }
  .contacts { list-style: none; color: var(--ink); font-size: 13.5px; line-height: 1.75; padding-top: 2px; }
  .contacts li { display: flex; align-items: center; gap: 8px; }
  .contacts svg { width: 11px; height: 11px; fill: var(--gold); flex: none; }

  .band-line {
    position: absolute; left: 0; right: 0; bottom: 22px;
    height: 2px; background: var(--navy);
  }
  .band {
    position: absolute; left: 0; right: 0; bottom: 0;
    height: 17px; background: var(--gold);
  }
</style>
</head>
<body>
  <section class="card card--front" aria-label="Card front">
    <div class="wordmark"><span class="wordmark__dot"></span>Heron</div>
  </section>

  <section class="card card--back" aria-label="Card back">
    <div class="wordmark"><span class="wordmark__dot"></span>Heron</div>

    <div class="details">
      <div class="person">
        <div class="person__name">DANA WHITFIELD</div>
        <div>Managing Director</div>
        <div>Your address, City</div>
        <div>State, Zip 1234</div>
      </div>
      <div class="divider"></div>
      <ul class="contacts">
        <li>
          <svg viewBox="0 0 24 24" aria-hidden="true"><path d="M6.6 10.8a15 15 0 0 0 6.6 6.6l2.2-2.2a1 1 0 0 1 1-.25 11.4 11.4 0 0 0 3.6.57 1 1 0 0 1 1 1V20a1 1 0 0 1-1 1A17 17 0 0 1 3 4a1 1 0 0 1 1-1h3.5a1 1 0 0 1 1 1c0 1.25.2 2.45.57 3.57a1 1 0 0 1-.25 1z"/></svg>
          555 018 247
        </li>
        <li>
          <svg viewBox="0 0 24 24" aria-hidden="true"><path d="M2 5h20v14H2z M2 5l10 8 10-8" /></svg>
          info@heronloans.com
        </li>
        <li>
          <svg viewBox="0 0 24 24" aria-hidden="true"><circle cx="12" cy="12" r="10"/></svg>
          www.heronloans.com
        </li>
      </ul>
    </div>

    <div class="band-line"></div>
    <div class="band"></div>
  </section>
</body>
</html>
```